Web Design Project

We wish to create a web based logistics exchange for heavy machinery and equipment catering to the mining, oil, gas and infrastructure industries. Customers interested in shipping equipment can post a load on the site and this would then be auctioned off through an online auction to prospective transport providers.Payments would be through direct bank transfer,pelko, quorvantix etc.
Both shippers and transport providers gain access via membership.
When a load is posted it would appear on the map indicating its location.Transport providers click on the icon of this map to access information of the pick up and delivery details as well as the load description.
The site would also have links to transport departments and equipment specification sites.
Advertising and merchandising are the other areas of revenue through the site

Target Market(s)

Shippers from Machinery Auction centres and Transport companies

Industry/Entity Type

Catering

Requirements
Must have
• The Logo of the company. The file is attached.

```html
<!DOCTYPE html>
<html lang="en">
<head>
<meta charset="utf-8">
<title>Haulvista – Heavy Equipment Logistics Exchange</title>
<link rel="stylesheet" href="https://fonts.googleapis.com/css2?family=Lato:ital,wght@0,300;0,400;0,700;0,900;1,300;1,400&display=swap">
<style>
  :root {
    --ink: #3a3a3a;
    --nav-ink: #6b6b6b;
    --brand-blue: #2a7cc0;
    --band-top: #3b8ad0;
    --band-bottom: #1d63a8;
    --orange-top: #ffb400;
    --orange-bottom: #f17a00;
    --hero-top: #e2e2e2;
    --hero-bottom: #ffffff;
    --machine-light: #f4c545;
    --machine-dark: #d48f16;
    --body-ink: #5a5a5a;
    --btn-top: #e4e4e4;
    --btn-bottom: #8e8e8e;
    --footer: #151515;
    --white: #ffffff;
    --divider: #e3e3e3;
  }
  * { box-sizing: border-box; margin: 0; padding: 0; }
  html, body { width: 983px; height: 1200px; overflow: hidden; }
  body {
    position: relative;
    background: var(--white);
    font-family: "Lato", sans-serif;
    color: var(--ink);
  }

  /* Header */
  .site-header { position: absolute; left: 0; top: 0; width: 983px; height: 109px; background: var(--white); }
  .brand { position: absolute; display: flex; align-items: center; gap: 12px; }
  .brand-mark { width: 34px; height: 34px; border-radius: 50%; background: var(--brand-blue); flex: none; }
  .brand-name { font-family: "Lato", sans-serif; font-weight: 700; letter-spacing: 2px; }
  .site-header .brand { left: 106px; top: 36px; }
  .site-header .brand-name { font-size: 30px; color: #1f2a3a; }
  .main-nav { position: absolute; left: 470px; top: 38px; display: flex; height: 44px; }
  .main-nav a {
    display: flex; align-items: center; padding: 0 23px;
    font-size: 13px; font-weight: 700; color: var(--nav-ink); text-decoration: none;
    border-left: 1px solid var(--divider);
  }
  .main-nav a:first-child { border-left: none; }

  /* Promo band */
  .promo-band {
    position: absolute; left: 0; top: 109px; width: 983px; height: 105px;
    background: linear-gradient(var(--band-top), var(--band-bottom));
  }
  .promo-title { position: absolute; left: 107px; top: 36px; font-size: 26px; font-weight: 300; color: var(--white); }
  .btn-join {
    position: absolute; left: 663px; top: 32px; width: 179px; height: 45px;
    border-radius: 3px; background: linear-gradient(var(--orange-top), var(--orange-bottom));
    box-shadow: 0 1px 2px rgba(0,0,0,.3);
    color: var(--white); font-size: 22px; font-weight: 900; text-align: center; line-height: 45px;
    text-shadow: 0 1px 1px rgba(0,0,0,.35); text-decoration: none;
  }

  /* Hero */
  .hero {
    position: absolute; left: 0; top: 214px; width: 983px; height: 344px;
    background: linear-gradient(var(--hero-top), var(--hero-bottom));
  }
  .hero-copy { position: absolute; left: 109px; top: 44px; width: 240px; font-size: 15px; font-weight: 300; line-height: 19.8px; color: var(--nav-ink); }
  .hero-copy strong { font-weight: 700; color: #555; }
  .btn-grey {
    display: block; position: absolute; border-radius: 2px;
    background: linear-gradient(var(--btn-top), var(--btn-bottom));
    box-shadow: 0 1px 2px rgba(0,0,0,.3);
    color: var(--white); font-weight: 700; text-align: center; text-decoration: none;
    text-shadow: 0 1px 1px rgba(0,0,0,.3);
  }
  .btn-learn { left: 109px; top: 256px; width: 120px; height: 28px; line-height: 28px; font-size: 15px; }
  .hero-visual {
    position: absolute; left: 362px; top: 54px; width: 466px; height: 246px;
    border-radius: 10px;
    background: linear-gradient(135deg, var(--machine-light) 0%, var(--machine-dark) 100%);
    box-shadow: 0 6px 16px rgba(0,0,0,.12);
  }

  /* Features */
  .content-panel { position: absolute; z-index: 2; left: 98px; top: 558px; width: 786px; height: 479px; background: var(--white); }
  .feature { position: absolute; width: 230px; }
  .feature h2 { font-size: 27px; font-weight: 300; color: var(--brand-blue); white-space: nowrap; }
  .feature p { margin: 16px 0 0 7px; width: 212px; font-size: 11px; font-weight: 300; line-height: 14px; color: var(--body-ink); }
  .feature .btn-more { position: relative; margin: 9px 0 0 7px; width: 50px; height: 19px; line-height: 19px; font-size: 10.5px; }

  /* Footer */
  .site-footer { position: absolute; z-index: 1; left: 0; top: 1003px; width: 983px; height: 197px; background: var(--footer); }
  .footer-nav { position: absolute; left: 142px; top: 116px; font-size: 12.5px; font-weight: 300; font-style: italic; color: var(--white); }
  .footer-nav a { color: var(--white); text-decoration: none; }
  .site-footer .brand { left: 680px; top: 82px; gap: 10px; }
  .site-footer .brand-mark { width: 26px; height: 26px; background: #9a9a9a; }
  .site-footer .brand-name { font-size: 22px; color: #d6d6d6; }
  .legal { position: absolute; right: 136px; top: 133px; font-size: 8.5px; font-style: italic; color: var(--white); }
</style>
</head>
<body>
  <header class="site-header">
    <div class="brand"><span class="brand-mark"></span><span class="brand-name">HAULVISTA</span></div>
    <nav class="main-nav">
      <a href="#">How it works</a>
      <a href="#">Who is using us?</a>
      <a href="#">Pricing</a>
      <a href="#">Contact</a>
    </nav>
  </header>

  <section class="promo-band">
    <h1 class="promo-title">Lorem Ipsum Consectetur Adipiscing Elit</h1>
    <a class="btn-join" href="#">Join us now</a>
  </section>

  <section class="hero">
    <p class="hero-copy"><strong>Duis aute irure dolor in reprehenderit in voluptate.</strong> Lorem ipsum dolor sit amet, consectetur adipisicing elit, sed do eiusmod tempor incididunt ut labore et dolore magna aliqua. Ut enim ad minim veniam, quis nostrud exercitation ullamco laboris nisi ut aliquip ex ea commodo consequat.</p>
    <a class="btn-grey btn-learn" href="#">Learn More</a>
    <div class="hero-visual" role="img" aria-label="Yellow wheeled excavator with extended arm and bucket"></div>
  </section>

  <main class="content-panel">
    <article class="feature" style="left:26px; top:67px;">
      <h2>Lorem Ipsum Elit</h2>
      <p>Lorem ipsum dolor sit amet, consectetur adipiscing elit. Curabitur lorem justo, euismod quis feugiat eu, malesuada eget erat. Class aptent taciti sociosqu ad litora torquent per conubia nostra, per inceptos himenaeos.</p>
      <a class="btn-grey btn-more" href="#">More</a>
    </article>
    <article class="feature" style="left:289px; top:67px;">
      <h2>Consectetur Elit</h2>
      <p>Lorem ipsum dolor sit amet, consectetur adipiscing elit. Curabitur lorem justo, euismod quis feugiat eu, malesuada eget erat. Class aptent taciti sociosqu ad litora torquent per conubia nostra, per inceptos himenaeos.</p>
      <a class="btn-grey btn-more" href="#">More</a>
    </article>
    <article class="feature" style="left:548px; top:67px;">
      <h2>Adipiscing Lorem</h2>
      <p>Lorem ipsum dolor sit amet, consectetur adipiscing elit. Curabitur lorem justo, euismod quis feugiat eu, malesuada eget erat. Class aptent taciti sociosqu ad litora torquent per conubia nostra, per inceptos himenaeos.</p>
      <a class="btn-grey btn-more" href="#">More</a>
    </article>
    <article class="feature" style="left:26px; top:271px;">
      <h2>Consectetur Elit</h2>
      <p>Lorem ipsum dolor sit amet, consectetur adipiscing elit. Curabitur lorem justo, euismod quis feugiat eu, malesuada eget erat. Class aptent taciti sociosqu ad litora torquent per conubia nostra, per inceptos himenaeos.</p>
      <a class="btn-grey btn-more" href="#">More</a>
    </article>
    <article class="feature" style="left:289px; top:271px;">
      <h2>Adipiscing Lorem</h2>
      <p>Lorem ipsum dolor sit amet, consectetur adipiscing elit. Curabitur lorem justo, euismod quis feugiat eu, malesuada eget erat. Class aptent taciti sociosqu ad litora torquent per conubia nostra, per inceptos himenaeos.</p>
      <a class="btn-grey btn-more" href="#">More</a>
    </article>
    <article class="feature" style="left:548px; top:271px;">
      <h2>Lorem Ipsum Elit</h2>
      <p>Lorem ipsum dolor sit amet, consectetur adipiscing elit. Curabitur lorem justo, euismod quis feugiat eu, malesuada eget erat. Class aptent taciti sociosqu ad litora torquent per conubia nostra, per inceptos himenaeos.</p>
      <a class="btn-grey btn-more" href="#">More</a>
    </article>
  </main>

  <footer class="site-footer">
    <nav class="footer-nav">
      <a href="#">Home</a> | <a href="#">How it works?</a> | <a href="#">Who is using us?</a> | <a href="#">Pricing</a> | <a href="#">Contact</a>
    </nav>
    <div class="brand"><span class="brand-mark"></span><span class="brand-name">HAULVISTA</span></div>
    <p class="legal">Terms of Use | Privacy Policy</p>
  </footer>
</body>
</html>
```